Redesign a Start-Up Dating Website

Website: https://morvelique.com.
Make sure the design has an island style theme.
I would like the 7 pages of my website to have a new and professional look. I want the same colors to remain, but I want a creative look for all the pages. This is a dating website that is in the startup stage. So, I want to give my entire website a custom makeover. I want something that will stand out from the other dating sites. Something that will attract more people to want to use my services, and hopefully get new members.
Target Market(s)
Dating
Industry/Entity Type
Dating
Coding
Coded - Design and coding required
Number of Pages Required
5+ page
Font styles to use
Other font styles liked:
- Decorative, San Serif
Requirements
Must have
- The design must have the original colors and a stylish font to go along. The design must be creative, welcoming, and professional. I would like an island style theme for the website. This is a dating website so make sure that the design is tailored to that aspect.
Nice to have
- It would be nice to have a decorative font and a professional style on all the pages. Make sure the design will be mobile responsive and friendly for all the pages on the website.
Should not have
- The design should not be bland and uncreative.

```html
<!DOCTYPE html>
<html lang="en">
<head>
<meta charset="utf-8">
<title>Morvelique — Dating</title>
<link rel="stylesheet" href="https://fonts.googleapis.com/css2?family=Open+Sans:wght@400;600;700&family=Roboto+Slab:wght@400;700&display=swap">
<style>
:root{
  --purple:#6b3f98;
  --purple-panel:#7a4fa6;
  --purple-dark:#4a2768;
  --teal:#2fae98;
  --teal-band:#45bca8;
  --teal-head:#2ea792;
  --teal-body:#38b39e;
  --orange:#f28a1c;
  --beige:#f5f0eb;
  --ink:#333;
  --grey:#666;
  --white:#fff;
}
*{box-sizing:border-box;margin:0;padding:0}
html,body{width:1200px;height:3010px;overflow:hidden}
body{position:relative;background:var(--white);font-family:"Open Sans",Arial,sans-serif;color:var(--ink)}
.abs{position:absolute}
.slab{font-family:"Roboto Slab",Georgia,serif}

/* hero */
.hero{left:0;top:0;width:1200px;height:680px;background:linear-gradient(90deg,#8a6a52 0%,#c9a98a 30%,#e6d6c6 55%,#e9ddd2 100%)}
.hero-wave{left:0;top:540px;width:1200px;height:160px}

/* header */
.site-header{left:132px;top:0;width:932px;height:108px;background:var(--white);border-radius:0 0 14px 14px}
.brand{left:22px;top:22px;display:flex;align-items:center;gap:10px}
.brand-dot{width:44px;height:44px;border-radius:50%;background:var(--orange)}
.brand-name{font-weight:700;font-size:42px;color:var(--teal);line-height:1}
.btn-small{top:20px;height:36px;color:var(--white);font-size:13px;display:flex;align-items:center;justify-content:center;gap:6px;border-radius:3px}
.btn-login{left:728px;width:78px;background:var(--orange)}
.btn-register{left:816px;width:96px;background:var(--purple)}
.main-nav{top:74px;left:434px;display:flex;font-size:13px;color:#555}

/* quick search */
.quick-search{left:602px;top:170px;width:460px;height:406px;background:var(--purple-panel);border-radius:3px}
.qs-title{left:22px;top:14px;display:flex;align-items:center;gap:12px;color:var(--white);font-size:32px}
.qs-rule{left:0;top:72px;width:460px;height:1px;background:rgba(255,255,255,.2)}
.qs-label{color:var(--white);font-size:15px}
.qs-select{height:42px;background:var(--white);border-radius:3px;font-size:13px;color:#444;display:flex;align-items:center;justify-content:space-between;padding:0 12px}
.qs-btn{left:22px;top:344px;width:96px;height:40px;background:var(--orange);color:var(--white);font-family:"Roboto Slab",serif;font-size:15px;display:flex;align-items:center;justify-content:center;border-radius:3px}
.hero-tagline{left:636px;top:594px;font-size:24px;color:#222}

/* intro */
.intro-title{left:0;top:766px;width:1200px;text-align:center;font-size:48px;color:var(--purple)}
.intro-sub{left:0;width:1200px;text-align:center;font-size:26px;color:var(--teal)}
.btn-orange{background:var(--orange);color:var(--white);font-family:"Roboto Slab",serif;display:flex;align-items:center;justify-content:center;border-radius:2px}

/* profiles */
.section-rule{top:1068px;height:1px;background:#ccc}
.profiles-title{left:0;top:1050px;width:1200px;text-align:center;font-size:24px;color:#555}
.profile{top:1108px;width:160px;text-align:center}
.profile-photo{width:160px;height:160px;background:linear-gradient(160deg,#d8d2cc,#b59c88 60%,#7b6658)}
.profile-name{margin-top:12px;font-size:14px;color:#444}
.profile-tag{font-size:11px;color:#888;margin-top:2px}
.carousel-arrow{top:1176px;width:22px;height:22px;border:1px solid #bbb;display:flex;align-items:center;justify-content:center}

/* steps band */
.steps{left:0;top:1388px;width:1200px;height:318px;background:var(--teal-band)}
.step{top:62px;width:290px;text-align:center;color:var(--white)}
.step-icon{width:74px;height:74px;border-radius:50%;background:var(--white);margin:0 auto;display:flex;align-items:center;justify-content:center}
.step-title{margin-top:26px;font-size:24px}
.step-text{margin-top:8px;font-size:12px;line-height:20px}

/* join */
.join-title{left:132px;top:1764px;font-size:25px;color:var(--teal)}
.join-text{left:132px;top:1814px;width:636px;font-size:12.6px;line-height:21.4px;color:#555}
.join-photo{left:814px;top:1760px;width:252px;height:252px;border-radius:50%;background:radial-gradient(circle at 50% 40%,#f1d9c0,#c99a72 60%,#8fb7c8)}

/* plans */
.plans{left:0;top:2110px;width:1200px;height:770px;background:var(--beige)}
.plans-title{left:0;top:112px;width:1200px;text-align:center;font-size:48px;color:var(--purple)}
.plans-sub{left:0;width:1200px;text-align:center;font-size:25px;color:var(--teal)}
.plan{top:284px;width:216px;height:408px;background:var(--teal-body)}
.plan-head{height:150px;background:var(--teal-head);text-align:center;color:var(--white);padding-top:22px}
.plan-name{font-size:23px;font-weight:700}
.plan-price{margin-top:18px;font-size:24px;font-weight:700;line-height:1.1}
.plan-term{font-size:24px}
.plan-features{text-align:center;color:var(--white);font-size:10.5px;line-height:23px;margin-top:20px}
.plan-btn{left:38px;top:332px;width:140px;height:48px;font-size:16px}

/* footer */
.site-footer{left:0;top:2880px;width:1200px;height:130px;background:var(--purple-dark);color:#ddd}
.footer-nav{left:132px;top:36px;font-size:12px}
.footer-copy{left:132px;top:62px;font-size:12px}
.social{top:36px;width:34px;height:34px;border-radius:50%;border:1px solid rgba(255,255,255,.55)}
</style>
</head>
<body>

<div class="abs hero" role="img" aria-label="Photo of a smiling couple embracing in warm island sunlight"></div>
<svg class="abs hero-wave" viewBox="0 0 1200 160" aria-hidden="true">
  <path d="M0 130 C 150 70, 350 50, 520 70 C 640 85, 700 145, 820 140 C 960 135, 1100 90, 1200 60 L1200 160 L0 160 Z" fill="#fff"/>
  <path d="M0 130 C 150 70, 350 50, 520 70 L520 76 C 350 60, 150 84, 0 150 Z" fill="#f28a1c"/>
  <path d="M700 142 C 820 152, 1000 122, 1200 60 L1200 76 C 1000 136, 820 162, 700 148 Z" fill="#6b3f98"/>
</svg>

<header class="abs site-header">
  <div class="abs brand"><span class="brand-dot"></span><span class="brand-name">Morvelique</span></div>
  <div class="abs btn-small btn-login">
    <svg width="12" height="12" viewBox="0 0 12 12"><path d="M1 6h7M5 3l3 3-3 3M9 1h2v10H9" stroke="#fff" stroke-width="1.5" fill="none"/></svg>Log in</div>
  <div class="abs btn-small btn-register">
    <svg width="12" height="12" viewBox="0 0 12 12"><rect x="1" y="2" width="8" height="9" stroke="#fff" stroke-width="1.3" fill="none"/><path d="M5 7l6-6" stroke="#fff" stroke-width="1.5"/></svg>Register</div>
  <nav class="abs main-nav">
    <span style="color:var(--teal)">Home</span>
    <span style="margin-left:32px">Search</span>
    <span style="margin-left:26px">Members</span>
    <span style="margin-left:28px">Extras</span>
    <span style="margin-left:26px">About</span>
    <span style="margin-left:24px">Premium</span>
    <span style="margin-left:28px">Contact</span>
  </nav>
</header>

<section class="abs quick-search">
  <div class="abs qs-title slab">
    <svg width="28" height="28" viewBox="0 0 28 28"><circle cx="11" cy="11" r="8" stroke="#fff" stroke-width="4" fill="none"/><path d="M17 17l8 8" stroke="#fff" stroke-width="4" stroke-linecap="round"/></svg>
    Quick Search</div>
  <div class="abs qs-rule"></div>
  <div class="abs qs-label slab" style="left:22px;top:84px">I am :</div>
  <div class="abs qs-label slab" style="left:238px;top:84px">Seeking A :</div>
  <div class="abs qs-select" style="left:22px;top:104px;width:200px">Man<span>⬍</span></div>
  <div class="abs qs-select" style="left:238px;top:104px;width:200px">Woman<span>⬍</span></div>
  <div class="abs qs-label slab" style="left:22px;top:170px">Age :</div>
  <div class="abs qs-label slab" style="left:238px;top:170px">To :</div>
  <div class="abs qs-select" style="left:22px;top:192px;width:200px">18<span>⬍</span></div>
  <div class="abs qs-select" style="left:238px;top:192px;width:200px">35<span>⬍</span></div>
  <div class="abs qs-label slab" style="left:22px;top:258px">Country :</div>
  <div class="abs qs-select" style="left:22px;top:280px;width:416px">Afghanistan<span>⬍</span></div>
  <div class="abs qs-btn">SEARCH</div>
</section>
<div class="abs hero-tagline">Let's Find Your Perfect Match Today</div>

<h1 class="abs intro-title slab" style="font-weight:400">Dating is <b>EASY</b> with Morvelique</h1>
<p class="abs intro-sub slab" style="top:836px">Sign-up for a 30 days free trial</p>
<p class="abs intro-sub slab" style="top:874px">Enjoy all the benefits morvelique has to offer with a full membership.</p>
<div class="abs btn-orange" style="left:406px;top:930px;width:384px;height:48px;font-size:15px">START MORVELIQUING WITH FREE SIGN-UP</div>

<div class="abs section-rule" style="left:132px;width:330px"></div>
<div class="abs section-rule" style="left:738px;width:330px"></div>
<h2 class="abs profiles-title slab" style="font-weight:400">Latest Added Profiles</h2>
<div class="abs carousel-arrow" style="left:70px"><svg width="8" height="8" viewBox="0 0 8 8"><path d="M6 0L2 4l4 4" stroke="#999" fill="none"/></svg></div>
<div class="abs carousel-arrow" style="left:1104px"><svg width="8" height="8" viewBox="0 0 8 8"><path d="M2 0l4 4-4 4" stroke="#999" fill="none"/></svg></div>
<div class="abs profile" style="left:132px"><div class="profile-photo" role="img" aria-label="Profile photo of Jacob"></div><div class="profile-name">Jacob</div><div class="profile-tag">Aliquam dignissim</div></div>
<div class="abs profile" style="left:325px"><div class="profile-photo" role="img" aria-label="Profile photo of Emma"></div><div class="profile-name">Emma</div><div class="profile-tag">Nulla porttitor</div></div>
<div class="abs profile" style="left:518px"><div class="profile-photo" role="img" aria-label="Profile photo of Mason" style="background:linear-gradient(160deg,#cfd6dc,#8aa0b8 60%,#4d6b95)"></div><div class="profile-name">Mason</div><div class="profile-tag">Nam tempus</div></div>
<div class="abs profile" style="left:711px"><div class="profile-photo" role="img" aria-label="Profile photo of Isabella" style="background:linear-gradient(160deg,#c9c4bf,#7d5a48 60%,#3b2a22)"></div><div class="profile-name">Isabella</div><div class="profile-tag">Duis hendrerit</div></div>
<div class="abs profile" style="left:904px"><div class="profile-photo" role="img" aria-label="Profile photo of William"></div><div class="profile-name">William</div><div class="profile-tag">Nam elementum</div></div>

<section class="abs steps">
  <div class="abs step" style="left:155px">
    <div class="step-icon"><svg width="30" height="30" viewBox="0 0 30 30"><rect x="5" y="4" width="17" height="22" rx="2" stroke="#6b3f98" stroke-width="2" fill="none"/><path d="M9 10h9M9 15h6M17 22l8-8 2 2-8 8h-2z" stroke="#6b3f98" stroke-width="2" fill="none"/></svg></div>
    <div class="step-title slab">Create a Profile</div>
    <div class="step-text">Let people know all about you, the good and the quirky show the world your true colors and find someone with the same unique qualities as you.</div>
  </div>
  <div class="abs step" style="left:451px">
    <div class="step-icon"><svg width="30" height="30" viewBox="0 0 30 30"><path d="M15 25L5 15a6 6 0 0 1 10-7 6 6 0 0 1 10 7z" fill="#6b3f98"/></svg></div>
    <div class="step-title slab">Find Matches</div>
    <div class="step-text">Browse other users and feel the excitement of getting your first message and getting to know potential dates in a safe and fun environment.</div>
  </div>
  <div class="abs step" style="left:775px">
    <div class="step-icon"><svg width="30" height="30" viewBox="0 0 30 30"><circle cx="11" cy="6" r="3" fill="#6b3f98"/><circle cx="19" cy="6" r="3" fill="#6b3f98"/><rect x="8" y="10" width="6" height="16" rx="2" fill="#6b3f98"/><rect x="16" y="10" width="6" height="16" rx="2" fill="#6b3f98"/></svg></div>
    <div class="step-title slab">Start Dating</div>
    <div class="step-text">Once you've found your potential soulmate, it's time to meet up and say 'Hello' to the start of your journey together.</div>
  </div>
</section>

<h2 class="abs join-title slab" style="font-weight:400">Join this community of &nbsp;1 morvelique members</h2>
<p class="abs join-text">Aliquam erat volutpat. Etiam quis aliquet risus. Duis ornare erat eget magna dapibus, in accumsan quam pharetra. Nam tempus, quam in bibendum vulputate, sapien dolor viverra nisl, vitae euismod elit turpis et nulla. Aliquam erat volutpat. Pellentesque blandit lacus eget nunc faucibus, et tincidunt eros viverra. Phasellus consequat sagittis nisi suscipit feugiat. Cras eget leo sed nunc hendrerit ultricies eu at nisl. Praesent iaculis faucibus urna sit amet lacinia. Maecenas consequat justo enim, ac mattis massa imperdiet quis. Fusce eget neque elit. Sed augue orci, elementum in magna congue, tincidunt vulputate erat. Aliquam consectetur orci molestie dictum molestie.</p>
<div class="abs btn-orange" style="left:132px;top:1984px;width:120px;height:46px;font-size:16px">JOIN NOW</div>
<div class="abs join-photo" role="img" aria-label="Happy couple in sunglasses enjoying a sunny beach day"></div>

<section class="abs plans">
  <h2 class="abs plans-title slab" style="font-weight:400">Membership Plans</h2>
  <p class="abs plans-sub slab" style="top:196px">Affordable</p>
  <p class="abs plans-sub slab" style="top:232px">Easy sign-up and cancellation processes</p>

  <div class="abs plan" style="left:132px">
    <div class="plan-head slab"><div class="plan-name">FREE</div><div class="plan-price">30-day</div><div class="plan-term">Free Trial</div></div>
    <div class="plan-features">Advanced &amp; Saved Search<br>Access &amp; Reply to Email Messages<br>Compose New Email Messages<br>Create Albums<br>Send Winks<br>Upload Audio/Photos &amp; Videos</div>
    <div class="abs btn-orange plan-btn">SIGN UP NOW</div>
  </div>
  <div class="abs plan" style="left:370px">
    <div class="plan-head slab"><div class="plan-name">Try it Out</div><div class="plan-price">$15</div><div class="plan-term">3 Months</div></div>
    <div class="plan-features">Aliquam ac elit vitae sapien<br>Nulla ut neque mattis<br>Nam ultrices orci nec<br>Proin ut enim blandit, egestas<br>Donec aliquam quam eget<br>Nunc pellentesque</div>
    <div class="abs btn-orange plan-btn">SIGN UP NOW</div>
  </div>
  <div class="abs plan" style="left:610px">
    <div class="plan-head slab"><div class="plan-name">Recommended</div><div class="plan-price">$10</div><div class="plan-term">6 Months</div></div>
    <div class="plan-features">Aliquam dignissim elit ne<br>Nulla porttitor nibh ut mi<br>Nam tempus augue<br>Vestibulum non ex quis mi<br>Duis hendrerit arcu ut sem<br>Pellentesque vehicula</div>
    <div class="abs btn-orange plan-btn">SIGN UP NOW</div>
  </div>
  <div class="abs plan" style="left:848px">
    <div class="plan-head slab"><div class="plan-name">Popular</div><div class="plan-price">$5</div><div class="plan-term">12 Months</div></div>
    <div class="plan-features">Integer ac est euismod<br>Nam elementum<br>Maecenas sed nibh sed<br>Vestibulum ut<br>Quisque blandit elit ut urna<br>Duis id quam auctor</div>
    <div class="abs btn-orange plan-btn">SIGN UP NOW</div>
  </div>
</section>

<footer class="abs site-footer">
  <div class="abs footer-nav">Home &nbsp;| &nbsp;Search &nbsp;| &nbsp;Members &nbsp;| &nbsp;Extras &nbsp;| &nbsp;About &nbsp;| &nbsp;Premium &nbsp;| &nbsp;Contact</div>
  <div class="abs footer-copy">Copyright &copy; 2017 Morvelique. &nbsp;All rights reserved.</div>
  <div class="abs social" style="left:836px"></div>
  <div class="abs social" style="left:884px"></div>
  <div class="abs social" style="left:932px"></div>
  <div class="abs social" style="left:980px"></div>
  <div class="abs social" style="left:1028px"></div>
</footer>

</body>
</html>
```